Corvel Capital LLC

Need Professional Business cards for New Investment Fund

Target Market(s)

High Quality investors

Industry/Entity Type

Financial

Contact Information for Business Card

Phone Number +1 555 284 6190
Name Lukas Varenko
Title Fund Manager
email lv@FundCorvel.com
Website www.FundCorvel.com

Colors

Designer to choose colors to be used in the design.

Requirements
Must have
• Must have our Logo and all of the above. Must be made so lettering and loge can be raised

```html
<!DOCTYPE html>
<html lang="en">
<head>
<meta charset="utf-8">
<title>Veltrana — Business Card</title>
<link rel="stylesheet" href="https://fonts.googleapis.com/css2?family=Jost:wght@400;500;600&family=Lato:wght@400&display=swap">
<style>
  :root {
    --stage: #2b2b2d;
    --card-top: #1b1c1e;
    --card-bottom: #29292a;
    --curve: #4b5447;
    --green: #39e61c;
    --white: #f1f1f1;
    --rule: #6a6a6a;
    --back: #18191a;
    --pattern: #202122;
  }
  * { margin: 0; padding: 0; box-sizing: border-box; }
  html, body { width: 1200px; height: 1108px; overflow: hidden; background: var(--stage); }
  .canvas {
    position: relative; width: 1200px; height: 1108px;
    display: flex; justify-content: center; align-items: center; gap: 80px;
  }
  .card {
    position: relative; width: 420px; height: 700px; border-radius: 26px; overflow: hidden;
  }
  .card--front { background: var(--card-bottom); }
  .front-top { position: absolute; inset: 0; width: 100%; height: 100%; }
  .brand {
    position: absolute; top: 160px; left: 0; right: 0;
    display: flex; justify-content: center; align-items: center; gap: 12px;
    font-family: "Jost", sans-serif; font-weight: 500; font-size: 50px;
    color: var(--green); letter-spacing: 1px;
  }
  .brand__dot { width: 20px; height: 20px; border-radius: 50%; background: var(--green); }
  .identity { position: absolute; top: 440px; left: 0; right: 0; text-align: center; }
  .identity__name {
    font-family: "Jost", sans-serif; font-weight: 600; font-size: 30px;
    color: var(--green); text-transform: uppercase; letter-spacing: 0.5px;
  }
  .identity__title { font-family: "Lato", sans-serif; font-size: 22px; color: var(--white); margin-top: 2px; }
  .icon-row { display: flex; align-items: center; justify-content: center; gap: 6px; margin: 14px 40px 12px; }
  .icon-row__rule { flex: 1; height: 1px; background: var(--rule); }
  .icon-row svg { width: 28px; height: 28px; }
  .contact { font-family: "Lato", sans-serif; font-size: 22px; line-height: 30px; color: var(--white); }
  .card--back { background: var(--back); }
  .back-pattern { position: absolute; inset: 0; background: linear-gradient(180deg, var(--pattern), var(--back)); }
  .back-brand {
    position: absolute; right: 60px; bottom: 200px;
    display: flex; align-items: center; gap: 8px;
    font-family: "Jost", sans-serif; font-weight: 500; font-size: 30px; color: var(--green);
  }
  .back-brand__dot { width: 12px; height: 12px; border-radius: 50%; background: var(--green); }
</style>
</head>
<body>
<main class="canvas">
  <section class="card card--front">
    <svg class="front-top" viewBox="0 0 420 700" aria-hidden="true">
      <path d="M0 0 H420 V400 C340 330 180 290 0 300 Z" fill="var(--card-top)"/>
      <path d="M0 300 C180 290 340 330 420 400 L420 408 C340 340 180 300 0 312 Z" fill="var(--curve)"/>
    </svg>
    <div class="brand"><span class="brand__dot"></span>Veltrana</div>
    <div class="identity">
      <p class="identity__name">Lukas Varenko</p>
      <p class="identity__title">Fund Manager</p>
      <div class="icon-row">
        <span class="icon-row__rule"></span>
        <svg viewBox="0 0 28 28" aria-label="Phone"><circle cx="14" cy="14" r="13" fill="var(--green)"/><path d="M9 8 l3 0 l1 4 l-2 1 a8 8 0 0 0 4 4 l1 -2 l4 1 l0 3 a2 2 0 0 1 -2 2 a12 12 0 0 1 -11 -11 a2 2 0 0 1 2 -2 z" fill="var(--card-bottom)"/></svg>
        <svg viewBox="0 0 28 28" aria-label="Email"><circle cx="14" cy="14" r="13" fill="var(--green)"/><rect x="7" y="9" width="14" height="10" fill="var(--card-bottom)"/><path d="M7 9 L14 15 L21 9" stroke="var(--green)" stroke-width="1.5" fill="none"/></svg>
        <svg viewBox="0 0 28 28" aria-label="Website"><circle cx="14" cy="14" r="13" fill="var(--green)"/><circle cx="14" cy="14" r="7" fill="none" stroke="var(--card-bottom)" stroke-width="2"/><ellipse cx="14" cy="14" rx="3" ry="7" fill="none" stroke="var(--card-bottom)" stroke-width="1.5"/><line x1="7" y1="14" x2="21" y2="14" stroke="var(--card-bottom)" stroke-width="1.5"/></svg>
        <span class="icon-row__rule"></span>
      </div>
      <p class="contact">+1 555 284 6190</p>
      <p class="contact">lv@FundCorvel.com</p>
      <p class="contact">www.FundCorvel.com</p>
    </div>
  </section>
  <section class="card card--back">
    <div class="back-pattern" role="img" aria-label="Faint repeating brand pattern across the card back"></div>
    <div class="back-brand"><span class="back-brand__dot"></span>Veltrana</div>
  </section>
</main>
</body>
</html>
```